New Business Card Design

We would like to refresh our business cards and make them look better. We are an IT company specialising in Cloud Services, IT Managed Services, software and hardware. I have attached a PSD of our current design. Also attached our logo.
Updates

I have uploaded all new logos in EPS format.

Can you please edit all designs to include a job title for Marcus Hollis, eg. General Manager

Industry/Entity Type

Software

Colors
ffffff

Requirements
Must have
• Please use white background.
Should not have
• Black background

```html
<!DOCTYPE html>
<html lang="en">
<head>
<meta charset="utf-8">
<title>Meridian Systems – Business Card</title>
<link href="https://fonts.googleapis.com/css2?family=Source+Sans+3:wght@400;600;700&display=swap" rel="stylesheet">
<style>
  :root{
    --stage:#e6e5ee;
    --card:#ffffff;
    --ink:#2c3036;
    --text:#3a3d42;
    --slate:#858f9b;
    --red:#d23a26;
    --rule:#d6d8dc;
  }
  *{margin:0;padding:0;box-sizing:border-box}
  html,body{width:1200px;height:987px;overflow:hidden;background:var(--stage);
    font-family:"Source Sans 3",Arial,sans-serif;color:var(--text)}
  .card{position:absolute;width:640px;height:390px;background:var(--card);
    border-radius:28px;overflow:hidden;box-shadow:0 6px 18px rgba(60,60,90,.18)}
  .card--back{left:500px;top:60px}
  .card--front{left:60px;top:530px}

  .brand{display:flex;align-items:center;gap:14px}
  .brand__mark{width:46px;height:46px;border-radius:50%;background:var(--red);flex:none}
  .brand__name{font-weight:600;font-size:34px;letter-spacing:.12em;color:var(--ink);line-height:1}

  .card--back .brand{position:absolute;left:0;right:0;top:140px;justify-content:center}
  .card--back .web{position:absolute;left:0;right:0;top:220px;text-align:center;
    font-size:22px;letter-spacing:.18em;color:var(--ink)}

  .card__band{position:absolute;inset:0}
  .card--front .brand{position:absolute;left:44px;top:92px}
  .card--front .brand__name{font-size:26px}
  .card--front .brand__mark{width:38px;height:38px}
  .divider{position:absolute;left:352px;top:60px;width:1px;height:190px;background:var(--rule)}
  .contacts{position:absolute;left:372px;top:84px;list-style:none}
  .contacts li{display:flex;align-items:center;gap:10px;height:34px;font-size:19px;color:var(--text)}
  .contacts svg{width:18px;height:18px;flex:none}
  .person{position:absolute;right:34px;bottom:14px;text-align:right;color:#fff}
  .person__name{font-weight:700;font-size:26px;line-height:1.1}
  .person__title{font-size:18px;line-height:1.2}
</style>
</head>
<body>

<section class="card card--back">
  <div class="brand">
    <span class="brand__mark"></span>
    <span class="brand__name">meridian systems</span>
  </div>
  <p class="web">www.meridiansys.com.au</p>
</section>

<section class="card card--front">
  <svg class="card__band" viewBox="0 0 640 390" preserveAspectRatio="none">
    <path class="band__fill" d="M0,130 C50,280 190,330 340,330 C450,330 540,300 640,262 L640,390 L0,390 Z" fill="var(--slate)"/>
    <path class="band__accent" d="M0,92 C20,190 70,250 150,276 C80,240 25,180 0,120 Z" fill="var(--red)"/>
    <path class="band__accent" d="M390,318 C480,316 570,290 640,244 L640,254 C570,298 480,322 390,318 Z" fill="var(--red)"/>
  </svg>

  <div class="brand">
    <span class="brand__mark"></span>
    <span class="brand__name">meridian systems</span>
  </div>

  <div class="divider"></div>

  <ul class="contacts">
    <li><svg viewBox="0 0 20 20"><circle cx="10" cy="10" r="9" fill="none" stroke="var(--red)" stroke-width="2"/><path d="M6.5,5.5 l2,0 1,2.5 -1.3,1 a6,6 0 0 0 2.8,2.8 l1,-1.3 2.5,1 0,2 a1,1 0 0 1 -1,1 A8,8 0 0 1 5.5,6.5 a1,1 0 0 1 1,-1z" fill="var(--red)"/></svg>07 3000 4815</li>
    <li><svg viewBox="0 0 20 20"><rect x="5" y="1" width="10" height="18" rx="2" fill="var(--red)"/><rect x="7" y="3.5" width="6" height="6" fill="#fff"/></svg>0400 555 172</li>
    <li><svg viewBox="0 0 20 20"><rect x="1" y="4" width="18" height="12" rx="1.5" fill="var(--red)"/><path d="M2,5 L10,11 L18,5" fill="none" stroke="#fff" stroke-width="1.6"/></svg>mhollis@meridiansys.com.au</li>
    <li><svg viewBox="0 0 20 20"><circle cx="10" cy="10" r="8.5" fill="var(--red)"/><g fill="none" stroke="#fff" stroke-width="1.2"><ellipse cx="10" cy="10" rx="3.5" ry="8.5"/><path d="M1.5,10 H18.5 M3,6 H17 M3,14 H17"/></g></svg>www.meridiansys.com.au</li>
  </ul>

  <div class="person">
    <p class="person__name">Marcus Hollis</p>
    <p class="person__title">General Manager</p>
  </div>
</section>

</body>
</html>
```